Business Card & Email Signature Design || Upmarket + Luxury

Rima Vale Honey, a New Zealand Manuka Honey company needs a Business Card & Email Signature design.

Our logo's are attached in Gold & Black versions, feel free to be creative with how you use the logo and it's patterns in your design.

Style:
- Looking for an Elegant, Luxurious, Upmarket feel.
- Black/Matte Black Card, Gold Foil, UV Embossing

Information to Add:

- Logo
- Company Name: Rima Vale Honey
- Name: Martin Holloway
- Title: Creative Director
- Phone: +64 2815 96 417
- Email: martin@rimavalehoney.example.nz
- Website: www.rimavalehoney.example.nz

- Socials: ***For email Signature Only***
- Facebook: https://www.facebook.com/rimavalehoney/
- Instagram: https://www.instagram.com/rimavalehoney/

Target Market(s)

Asia/Europe Luxury, Upmarket

Contact Information for Business Card

- Logo
- Name: Martin Holloway
- Phone: +64 2815 96 417

Font styles to use
Other font styles liked:
• Champagne & Limousines (Attached)

Requirements
Must have
• Business Card & Email Signature Design.

Looking for a Sleek, Luxury, Upmarket Design.

```html
<!DOCTYPE html>
<html lang="en">
<head>
<meta charset="utf-8">
<title>Rima Vale Honey — Business Card</title>
<link rel="stylesheet" href="https://fonts.googleapis.com/css2?family=Montserrat:wght@400;600&display=swap">
<style>
  :root {
    --backdrop: #4a4a4a;
    --card: #383838;
    --gold: #cdb36e;
    --gold-deep: #b8903f;
    --gold-light: #e6d39a;
  }
  * { margin: 0; padding: 0; box-sizing: border-box; }
  html, body { width: 963px; height: 1200px; overflow: hidden; }
  body {
    background: var(--backdrop);
    font-family: "Montserrat", sans-serif;
    position: relative;
  }
  .card {
    position: absolute;
    left: 232px;
    width: 556px;
    height: 316px;
    background: var(--card);
  }
  .card-front { top: 222px; }
  .card-back { top: 636px; }

  .identity { position: absolute; left: 54px; top: 54px; color: var(--gold); }
  .identity .name {
    font-weight: 600;
    font-size: 25px;
    letter-spacing: 0.2px;
    line-height: 1.1;
  }
  .identity .title {
    font-weight: 400;
    font-size: 13.5px;
    margin-top: 3px;
    letter-spacing: 0.3px;
  }
  .contacts { list-style: none; margin-top: 22px; }
  .contacts li {
    display: flex;
    align-items: center;
    font-size: 13.5px;
    line-height: 18.5px;
  }
  .contacts svg { width: 11px; height: 11px; margin-right: 13px; fill: var(--gold); }

  .motif {
    position: absolute;
    right: 0;
    top: 0;
    width: 270px;
    height: 316px;
    background: radial-gradient(ellipse at 70% 60%, rgba(60,120,200,0.35), rgba(120,60,160,0.15) 40%, rgba(30,30,30,0) 70%),
                radial-gradient(ellipse at 40% 30%, rgba(230,180,30,0.18), rgba(30,30,30,0) 50%);
  }

  .frame-outer {
    position: absolute;
    left: 18px; top: 16px; right: 16px; bottom: 16px;
    border: 2px solid var(--gold);
  }
  .frame-inner {
    position: absolute;
    left: 25px; top: 23px; right: 23px; bottom: 23px;
    border: 1px solid var(--gold-deep);
  }
  .emblem {
    position: absolute;
    left: 281px; top: 162px;
    width: 188px; height: 188px;
    margin: -94px 0 0 -94px;
    border: 1.5px solid var(--gold);
    border-radius: 50%;
    display: flex;
    align-items: center;
    justify-content: center;
  }
  .emblem .brand {
    color: var(--gold);
    font-weight: 600;
    font-size: 15px;
    letter-spacing: 2px;
    text-transform: uppercase;
    text-align: center;
    line-height: 1.5;
  }
</style>
</head>
<body>
  <section class="card card-front">
    <div class="identity">
      <h1 class="name">MARTIN HOLLOWAY</h1>
      <p class="title">Creative Director</p>
      <ul class="contacts">
        <li>
          <svg viewBox="0 0 24 24" aria-hidden="true"><path d="M6.6 10.8a15.1 15.1 0 0 0 6.6 6.6l2.2-2.2c.3-.3.7-.4 1-.2 1.1.4 2.3.6 3.6.6.6 0 1 .4 1 1V20c0 .6-.4 1-1 1A17 17 0 0 1 3 4c0-.6.4-1 1-1h3.5c.6 0 1 .4 1 1 0 1.3.2 2.5.6 3.6.1.3 0 .7-.2 1z"/></svg>
          +64 2815 96 417
        </li>
        <li>
          <svg viewBox="0 0 24 24" aria-hidden="true"><path d="M2 5h20v14H2z M2 6l10 7 10-7" /></svg>
          martin@rimavalehoney.example.nz
        </li>
        <li>
          <svg viewBox="0 0 24 24" aria-hidden="true"><circle cx="12" cy="12" r="10"/></svg>
          rimavalehoney.example.nz
        </li>
      </ul>
    </div>
    <div class="motif" role="img" aria-label="Large decorative bee motif in black gloss with coloured swirl inlays"></div>
  </section>

  <section class="card card-back">
    <div class="frame-outer"></div>
    <div class="frame-inner"></div>
    <div class="emblem">
      <p class="brand">Rima Vale<br>Honey</p>
    </div>
  </section>
</body>
</html>
```